Vorn upkeep KT Solar Venture

Solar power system install
Services and maintenance
wiring, Rewinding and Renovation
Switch Board Upgrade
Power and lighting point
t doesn’t matter how much you spend on quality parts, your solar system will let you down if your design and installation are sub-par. Have your solar system tailored and installed by our Master Electrician and Bright Grid Guild Accredited team.

Target Market(s)

sales and installed

Industry/Entity Type

Solar install and retailer

Contact Information for Business Card

Name , Email, Phone Number ,Business address,

Font styles to use
Serif

Colors
0054AA
0677BA
7BADD7
CADEEF
E8F1F8

Requirements
Must have
• clear and bright
Nice to have
• new design
Should not have
• unclear pictures

```html
<!DOCTYPE html>
<html lang="en">
<head>
<meta charset="utf-8">
<title>Vorn upkeep – KT Solar Venture business card</title>
<link rel="stylesheet" href="https://fonts.googleapis.com/css2?family=Roboto:wght@400;500&family=Roboto+Condensed:wght@700&display=swap">
<style>
  :root {
    --backdrop: #2f2f2f;
    --brand-blue: #0054AA;
    --mid-blue: #0677BA;
    --sky-blue: #7BADD7;
    --pale-blue: #CADEEF;
    --mist: #E8F1F8;
    --leaf-green: #6cb33f;
    --deep-green: #1f9a3a;
    --name-green: #7cc242;
    --band-grey: #e9e9e9;
    --ink: #1d1d1d;
    --white: #ffffff;
  }
  * { box-sizing: border-box; margin: 0; padding: 0; }
  html, body {
    width: 1200px; height: 1138px; overflow: hidden;
    background: var(--backdrop);
    font-family: "Roboto", Arial, sans-serif;
  }
  .card {
    position: absolute;
    border-radius: 16px;
    overflow: hidden;
    box-shadow: 0 4px 10px rgba(0,0,0,.35);
  }

  /* Front */
  .card-front {
    left: 274px; top: 185px; width: 623px; height: 377px;
    background: linear-gradient(115deg, var(--brand-blue) 0%, var(--mid-blue) 30%, #2a9a98 62%, var(--leaf-green) 100%);
  }
  .front-mark {
    position: absolute; left: 135px; top: 70px;
    display: flex; align-items: center; gap: 22px;
  }
  .mark-dot {
    width: 100px; height: 100px; border-radius: 50%;
    background: var(--mist);
  }
  .wordmark {
    font-family: "Roboto Condensed", "Arial Narrow", sans-serif;
    font-weight: 700; text-transform: uppercase;
    line-height: 1.05; letter-spacing: 1px;
  }
  .front-mark .wordmark { color: var(--white); font-size: 34px; }
  .service-band {
    position: absolute; left: 0; top: 240px; width: 100%; height: 73px;
    background: var(--band-grey);
    display: flex; flex-direction: column; justify-content: center; align-items: center;
    gap: 4px; color: var(--ink); font-size: 16.5px;
  }
  .front-web {
    position: absolute; left: 0; top: 333px; width: 100%;
    display: flex; justify-content: center; align-items: center; gap: 24px;
    color: var(--white); font-size: 16px;
  }
  .front-web .rule { width: 80px; height: 2px; background: var(--mist); opacity: .8; }

  /* Back */
  .card-back {
    left: 275px; top: 607px; width: 619px; height: 375px;
    background: var(--mist);
  }
  .back-shape { position: absolute; inset: 0; }
  .person {
    position: absolute; left: 43px; top: 68px; color: var(--white);
  }
  .person-name { color: var(--name-green); font-size: 26px; font-weight: 500; }
  .person-role { font-size: 16px; margin-top: 4px; }
  .address {
    position: absolute; left: 43px; top: 180px; color: var(--white);
    font-size: 16px; line-height: 24px;
  }
  .contact-list {
    position: absolute; left: 43px; top: 234px; list-style: none;
    color: var(--white); font-size: 16px;
  }
  .contact-list li { display: flex; align-items: center; height: 24px; }
  .contact-list svg { width: 15px; height: 15px; margin-right: 16px; fill: var(--name-green); }
  .back-mark {
    position: absolute; left: 355px; top: 75px; width: 240px;
    display: flex; flex-direction: column; align-items: center; gap: 22px;
  }
  .back-mark .mark-dot { width: 110px; height: 110px; background: var(--pale-blue); }
  .back-mark .wordmark { color: var(--brand-blue); font-size: 29px; text-align: center; }
</style>
</head>
<body>

<section class="card card-front">
  <div class="front-mark">
    <span class="mark-dot"></span>
    <div class="wordmark">Vorn upkeep<br>KT Solar Venture</div>
  </div>
  <div class="service-band">
    <p>Solar Power System Install &nbsp;|&nbsp; Wiring, Rewinding &amp; Renovation</p>
    <p>Services &amp; Maintenance &nbsp;|&nbsp; Switch Board Upgrade &nbsp;|&nbsp; Power &amp; Lighting Point</p>
  </div>
  <div class="front-web">
    <span class="rule"></span>
    <span>www.ktsolarventure.com</span>
    <span class="rule"></span>
  </div>
</section>

<section class="card card-back">
  <svg class="back-shape" viewBox="0 0 619 375" preserveAspectRatio="none">
    <defs>
      <linearGradient id="panelBlue" x1="0" y1="0" x2="0" y2="1">
        <stop offset="0" stop-color="#0a4b92"/>
        <stop offset="1" stop-color="#1a7fc6"/>
      </linearGradient>
    </defs>
    <path d="M0,0 H392 Q256,187 396,375 H0 Z" fill="var(--deep-green)"/>
    <path d="M0,0 H385 Q250,187 389,375 H0 Z" fill="url(#panelBlue)"/>
  </svg>

  <div class="person">
    <h1 class="person-name">Ravel Quinn Ashby</h1>
    <p class="person-role">Managing Director</p>
  </div>
  <p class="address">58 Ledger Row, Fernhill,<br>Oakvale, US 204518</p>
  <ul class="contact-list">
    <li><svg viewBox="0 0 16 16"><path d="M3 1h3l1.5 4-2 1.5a9 9 0 0 0 4 4l1.5-2 4 1.5v3a1 1 0 0 1-1 1A13 13 0 0 1 2 2a1 1 0 0 1 1-1z"/></svg>555-010-2468</li>
    <li><svg viewBox="0 0 16 16"><path d="M1 3h14v10H1z M1 3l7 6 7-6" fill="none" stroke="var(--name-green)" stroke-width="1.6"/></svg>ravel@ktsolarventure.com</li>
    <li><svg viewBox="0 0 16 16"><circle cx="8" cy="8" r="6.5" fill="none" stroke="var(--name-green)" stroke-width="1.5"/><path d="M1.5 8h13M8 1.5c-3 3.5-3 9.5 0 13M8 1.5c3 3.5 3 9.5 0 13" fill="none" stroke="var(--name-green)" stroke-width="1.2"/></svg>www.ktsolarventure.com</li>
  </ul>

  <div class="back-mark">
    <span class="mark-dot"></span>
    <div class="wordmark">Vorn upkeep<br>KT Solar Venture</div>
  </div>
</section>

</body>
</html>
```